Business cards to launch an education platform

Hi,
I am looking at having new business cards designed.
I am a startup, developing a web platform for schools and university, the education world. It's an online assessment system.
I would like a card that looks classy, and that is using the colors and the font of my logo.

I have attached:
1) my logo
2) A business card that I have designed quickly so you can have all the information required in the card, but I really don't like it.
3) The font that I am using (Lato Regular) to design my web platform
4) Some screenshots of my web platform so you can have a look at the style that I have.

Target Market(s)

Major market: Education system: Schools and university
Minor markets: Business in general

Industry/Entity Type

Business

Contact Information for Business Card

Clara Fenwick
Director

M: 0437 518 902
E: clara.fenwick@amberLoomSystems.com.au

Requirements
Must have
• The colors of my logo

```html
<!DOCTYPE html>
<html lang="en">
<head>
<meta charset="utf-8">
<title>Amber Loom Systems – Business Card</title>
<link rel="stylesheet" href="https://fonts.googleapis.com/css2?family=Lato:wght@400;700&display=swap">
<style>
  :root {
    --backdrop: #2b2724;
    --card: #0c0c0e;
    --card-edge: #1a1a1d;
    --brand-blue: #2f8fd6;
    --accent-blue: #3fb2ea;
    --text-light: #e4e6ea;
    --text-muted: #c9ccd2;
  }

  * { margin: 0; padding: 0; box-sizing: border-box; }

  html, body {
    width: 1200px;
    height: 900px;
    overflow: hidden;
    background: var(--backdrop);
    font-family: "Lato", sans-serif;
  }

  .canvas {
    position: relative;
    width: 1200px;
    height: 900px;
  }

  .card {
    position: absolute;
    width: 520px;
    height: 316px;
    background: var(--card);
    border: 1px solid var(--card-edge);
    box-shadow: 0 18px 40px rgba(0, 0, 0, 0.45);
  }

  .card--front { left: 50px;  top: 292px; }
  .card--back  { left: 630px; top: 292px; }

  /* Front: company name */
  .brand {
    position: absolute;
    left: 40px;
    top: 108px;
    display: flex;
    align-items: center;
    gap: 14px;
  }

  .brand__mark {
    width: 58px;
    height: 58px;
    flex: none;
    background: var(--brand-blue);
  }

  .brand__name {
    color: var(--brand-blue);
    font-size: 24px;
    font-weight: 400;
    letter-spacing: 2px;
    line-height: 1.15;
  }

  .brand__line { display: block; white-space: nowrap; }

  /* Front: contact block */
  .contact {
    position: absolute;
    right: 34px;
    top: 150px;
    text-align: right;
  }

  .contact__name {
    color: var(--accent-blue);
    font-size: 21px;
    font-weight: 400;
    line-height: 1.1;
    white-space: nowrap;
  }

  .contact__role {
    color: var(--text-muted);
    font-size: 13px;
    margin-top: 2px;
  }

  .contact__list {
    list-style: none;
    margin-top: 24px;
  }

  .contact__item {
    display: flex;
    justify-content: flex-end;
    align-items: center;
    gap: 8px;
    color: var(--text-light);
    font-size: 14px;
    line-height: 20px;
    white-space: nowrap;
  }

  .contact__icon {
    width: 12px;
    height: 12px;
    flex: none;
  }

  .contact__email {
    position: absolute;
    right: 70px;
    bottom: 26px;
    color: var(--text-light);
    font-size: 15px;
    white-space: nowrap;
  }

  /* Back */
  .back-brand {
    position: absolute;
    inset: 0;
    display: flex;
    align-items: center;
    justify-content: center;
    gap: 16px;
  }

  .back-brand__mark {
    width: 44px;
    height: 44px;
    background: var(--brand-blue);
  }

  .back-brand__name {
    color: var(--brand-blue);
    font-size: 28px;
    font-weight: 400;
    letter-spacing: 2px;
    white-space: nowrap;
  }
</style>
</head>
<body>
<main class="canvas">

  <section class="card card--front" aria-label="Business card front">
    <div class="brand">
      <span class="brand__mark" aria-hidden="true"></span>
      <span class="brand__name">
        <span class="brand__line">Amber Loom</span>
        <span class="brand__line">Systems</span>
      </span>
    </div>

    <div class="contact">
      <p class="contact__name">Clara Fenwick</p>
      <p class="contact__role">Director</p>
      <ul class="contact__list">
        <li class="contact__item">
          <span>0437 518 902</span>
          <svg class="contact__icon" viewBox="0 0 24 24" aria-hidden="true">
            <path fill="#3fb2ea" d="M6.6 10.8a15.1 15.1 0 0 0 6.6 6.6l2.2-2.2c.3-.3.7-.4 1-.2 1.1.4 2.3.6 3.6.6.6 0 1 .4 1 1V20c0 .6-.4 1-1 1A17 17 0 0 1 3 4c0-.6.4-1 1-1h3.5c.6 0 1 .4 1 1 0 1.3.2 2.5.6 3.6.1.3 0 .7-.2 1z"/>
          </svg>
        </li>
        <li class="contact__item">
          <svg class="contact__icon" viewBox="0 0 24 24" aria-hidden="true">
            <rect x="2" y="5" width="20" height="14" rx="1.5" fill="#3fb2ea"/>
            <path d="M3 6l9 7 9-7" fill="none" stroke="#0c0c0e" stroke-width="1.8"/>
          </svg>
        </li>
      </ul>
    </div>

    <p class="contact__email">clara.fenwick@amberLoomSystems.com.au</p>
  </section>

  <section class="card card--back" aria-label="Business card back">
    <div class="back-brand">
      <span class="back-brand__mark" aria-hidden="true"></span>
      <span class="back-brand__name">Amber Loom Systems</span>
    </div>
  </section>

</main>
</body>
</html>
```